Realtor branding business card

modern, simple and self branding. Broker office logo needs to be used but not emphasized. Looking to brand myself

Target Market(s)

buyers, sellers and investors

Industry/Entity Type

Realtor

Contact Information for Business Card

Sample of my current business card on file

Requirements
Must have
• my website - tobiasmerrowkl.com
• Realtor logo
• Fair housing logo
Nice to have
• Colors from office logo but not a must
Should not have
• Do not want headshot

```html
<!DOCTYPE html>
<html lang="en">
<head>
<meta charset="utf-8">
<title>Tobias Merrow — Realtor Business Card</title>
<link rel="stylesheet" href="https://fonts.googleapis.com/css2?family=Montserrat:wght@400;500;700;800&display=swap">
<style>
  :root {
    --stage: #1e1e1e;
    --card: #2f2b7c;
    --accent: #e1262d;
    --ink: #ffffff;
    --badge: rgba(255, 255, 255, 0.85);
  }
  * { box-sizing: border-box; margin: 0; padding: 0; }
  html, body { width: 1200px; height: 900px; overflow: hidden; }
  body {
    background: var(--stage);
    font-family: "Montserrat", sans-serif;
    color: var(--ink);
    position: relative;
  }
  .card {
    position: absolute;
    width: 640px;
    height: 366px;
    background: var(--card);
    border-bottom: 8px solid var(--accent);
  }
  .card--front { left: 360px; top: 48px; }
  .card--back  { left: 200px; top: 478px; }

  .brand { display: flex; align-items: center; gap: 12px; }
  .brand__mark { width: 16px; height: 16px; background: var(--accent); flex: none; }
  .brand__name {
    font-weight: 800;
    font-size: 26px;
    line-height: 1.1;
    color: var(--ink);
  }

  /* Front: personal name leads, broker sits below it */
  .front__agent {
    position: absolute;
    left: 0; right: 0; top: 104px;
    text-align: center;
    font-weight: 700;
    font-size: 34px;
    letter-spacing: 1px;
    text-transform: uppercase;
  }
  .front__role {
    position: absolute;
    left: 0; right: 0; top: 150px;
    text-align: center;
    font-size: 17px;
    color: var(--accent);
    font-weight: 500;
  }
  .card--front .brand {
    position: absolute;
    left: 0; right: 0; top: 210px;
    justify-content: center;
  }
  .card--front .brand__name { font-size: 18px; font-weight: 700; }
  .card--front .site {
    position: absolute;
    left: 0; right: 0; bottom: 26px;
    text-align: center;
    font-size: 16px;
  }
  .site__name { color: var(--accent); }

  /* Back */
  .card--back .brand {
    position: absolute;
    left: 48px; top: 116px;
    width: 270px;
  }
  .badges {
    position: absolute;
    left: 48px; bottom: 36px;
    display: flex; gap: 14px;
  }
  .badge { width: 34px; height: 34px; background: var(--badge); }
  .divider {
    position: absolute;
    left: 350px; top: 40px;
    width: 2px; height: 270px;
    background: var(--accent);
  }
  .contact {
    position: absolute;
    left: 378px; top: 40px;
    width: 250px;
  }
  .contact__name {
    color: var(--accent);
    font-weight: 700;
    font-size: 22px;
    letter-spacing: 0.5px;
    text-transform: uppercase;
    white-space: nowrap;
  }
  .contact__role { font-size: 17px; margin-top: 2px; }
  .contact__list { list-style: none; margin-top: 16px; }
  .contact__item {
    display: flex; align-items: center; gap: 10px;
    font-size: 16px; line-height: 25px; white-space: nowrap;
  }
  .contact__item svg { width: 14px; height: 14px; flex: none; }
  .contact__address { font-size: 17px; margin-top: 14px; line-height: 25px; }
</style>
</head>
<body>

<section class="card card--front">
  <p class="front__agent">Tobias Merrow</p>
  <p class="front__role">Realtor</p>
  <div class="brand">
    <span class="brand__mark"></span>
    <span class="brand__name">Keystone Harbor Realty</span>
  </div>
  <p class="site">www.<span class="site__name">tobiasmerrowkl</span>.com</p>
</section>

<section class="card card--back">
  <div class="brand">
    <span class="brand__mark"></span>
    <span class="brand__name">Keystone Harbor<br>Realty</span>
  </div>
  <div class="badges">
    <span class="badge" role="img" aria-label="Realtor association badge"></span>
    <span class="badge" role="img" aria-label="Equal housing opportunity badge"></span>
  </div>
  <div class="divider"></div>
  <div class="contact">
    <h1 class="contact__name">Tobias Merrow</h1>
    <p class="contact__role">Realtor</p>
    <ul class="contact__list">
      <li class="contact__item">
        <svg viewBox="0 0 14 14" fill="none" stroke="#e1262d" stroke-width="1.4"><rect x="3.5" y="1" width="7" height="12" rx="1.2"/><line x1="6" y1="11" x2="8" y2="11"/></svg>
        555. 201. 4418
      </li>
      <li class="contact__item">
        <svg viewBox="0 0 14 14" fill="#e1262d"><path d="M3 1.5l2.2 0.2 1 3-1.4 1a7 7 0 0 0 3.5 3.5l1-1.4 3 1 .2 2.2c-.3.9-1.2 1.5-2.2 1.4C5.5 12 2 8.5 1.6 3.7 1.5 2.7 2.1 1.8 3 1.5z"/></svg>
        555. 630. 2900
      </li>
      <li class="contact__item">
        <svg viewBox="0 0 14 14" fill="none" stroke="#e1262d" stroke-width="1.3"><rect x="1" y="3" width="12" height="8.5" rx="1"/><polyline points="1.5,3.5 7,8 12.5,3.5"/></svg>
        info@tobiasmerrowkl.com
      </li>
      <li class="contact__item">
        <svg viewBox="0 0 14 14" fill="none" stroke="#e1262d" stroke-width="1.2"><circle cx="7" cy="7" r="5.8"/><ellipse cx="7" cy="7" rx="2.6" ry="5.8"/><line x1="1.2" y1="7" x2="12.8" y2="7"/></svg>
        <span>www.<span class="site__name">tobiasmerrowkl</span>.com</span>
      </li>
    </ul>
    <p class="contact__address">48 Larkfield Avenue<br>Cedar Hollow, FL 32900</p>
  </div>
</section>

</body>
</html>
```